Motivational Poster Design Project

I would like to create a poster with some of my favorite quotes to hang in my office. I did a similar project in 2012 and I've uploaded the top 2 designs so you can get a better idea of what I'm looking for. I will provide feedback on your design within 24 hours of receiving it.

The poster must contain the following quotes:

"You’re only given a little spark of madness. You mustn’t lose it.”
- Dorian Fletcher

“The most contrarian thing of all is not to oppose the crowd but to think for yourself.”
- Marcus Olden

"I constantly see people rise in life who are not the smartest, sometimes not even the most diligent, but they are learning machines. They go to bed every night a little wiser than they were when they got up and boy does that help, particularly when you have a long run ahead of you."
- Frankie Dalgarth

“In theory, there’s no difference between theory and practice. But, in practice, there is.”
- Kees R. T. Ter Haverkamp

"At the end of the day, a reactionary life is a normal life. One thing is consistent in every remarkable person: they decide to do something remarkable. Don’t let the world choose who you become."
- Rohan Kapadia

“It usually takes 3-4 months to try enough that you can do a proper 80/20 analysis, then two months to design systems to scale what *is* working.”
-Ned Yarrow

“Authority is 20 percent given, 80 percent taken.”
- Glenn Mosbacker

“Your actions are consistent with the way the world occurs to you.”
- Dieter Kolbach

Project Deadline Extended
Reason: I am going to be travelling with no access to internet until January 5th, 2015. I am extending the project deadline until 12/31/14 and I'll make a final decision during the 1st week of January.

Target Market(s)

Personal Project

Industry/Entity Type

Learning

Requirements
Must have
• The poster will be 24" high x 36" long and printed on canvas, so the image you create needs to have a resolution of at least 2700 x 3900.
Nice to have
• I don't have an exact vision for how the poster should look, so I am totally open to you using your creativity to develop, arrange and present the content as you'd like.
• That said, I would like an image (photo or posterized image) of the person being quoted along with each quote. I do not have specific images that I would like you to use, so you will need to find the images on your own. The images don't need to be perfect... I am more interested in the poster relating the essence of the quotes and the people being quoted than I am in perfect photographic images of the people being quoted.

```html
<!DOCTYPE html>
<html lang="en">
<head>
<meta charset="utf-8">
<title>Quotes Poster</title>
<link rel="stylesheet" href="https://fonts.googleapis.com/css2?family=Roboto+Condensed:ital,wght@1,300;1,400&family=Parisienne&display=swap">
<style>
  :root {
    --wood-light: #c9a272;
    --wood-mid: #a8794a;
    --wood-dark: #6e4a2a;
    --band-orange: #c8742c;
    --band-blue: #1f3d8f;
    --band-red: #bd3330;
    --band-green: #5e8c2b;
    --band-brown: #7b4b27;
    --band-olive: #9c8b1f;
    --band-purple: #5a2a6d;
    --band-black: #2b2a25;
    --ink: #f4ede2;
    --portrait-tone: #8c6a55;
  }
  * { box-sizing: border-box; margin: 0; padding: 0; }
  html, body { width: 800px; height: 1200px; overflow: hidden; }
  body { background: #ffffff; }
  .poster {
    position: relative;
    width: 800px;
    height: 1200px;
    overflow: hidden;
    background:
      radial-gradient(ellipse at 50% 45%, transparent 40%, rgba(50, 28, 10, 0.55) 100%),
      linear-gradient(100deg, var(--wood-mid), var(--wood-light) 45%, var(--wood-mid) 70%, var(--wood-dark));
  }
  .band {
    position: absolute;
    left: 28px;
    width: 750px;
    display: flex;
    align-items: center;
    box-shadow: 0 3px 8px rgba(0, 0, 0, 0.35);
  }
  .portrait {
    flex: none;
    width: 116px;
    height: 116px;
    margin-left: 36px;
    border-radius: 50%;
    background: radial-gradient(circle at 50% 40%, #b99883, var(--portrait-tone) 55%, #2a1f1a);
    border: 3px solid rgba(0, 0, 0, 0.55);
  }
  .quote {
    flex: 1;
    padding: 0 22px 0 18px;
    text-align: center;
    color: var(--ink);
  }
  .quote-text {
    font-family: "Roboto Condensed", "Arial Narrow", sans-serif;
    font-style: italic;
    font-weight: 300;
    font-size: 18.5px;
    line-height: 1.3;
  }
  .quote-author {
    font-family: "Parisienne", cursive;
    font-size: 25px;
    line-height: 1.2;
    margin-top: 4px;
    opacity: 0.92;
  }
  .band-1 { top: -6px; left: 22px; height: 158px; background: var(--band-orange); transform: rotate(-2deg); }
  .band-2 { top: 156px; height: 122px; background: var(--band-blue); }
  .band-3 { top: 278px; height: 164px; background: var(--band-red); transform: rotate(1deg); }
  .band-4 { top: 446px; height: 132px; background: var(--band-green); transform: rotate(-0.5deg); }
  .band-5 { top: 584px; height: 150px; background: var(--band-brown); transform: rotate(-2deg); }
  .band-6 { top: 736px; height: 140px; background: var(--band-olive); }
  .band-7 { top: 866px; height: 146px; background: var(--band-purple); transform: rotate(-2deg); }
  .band-8 { top: 1022px; height: 148px; background: var(--band-black); transform: rotate(1deg); }
</style>
</head>
<body>
<main class="poster">
  <section class="band band-1">
    <div class="portrait" role="img" aria-label="Portrait of Dorian Fletcher"></div>
    <div class="quote">
      <p class="quote-text">“You’re only given a little spark of madness. You mustn’t lose it.”</p>
      <p class="quote-author">- Dorian Fletcher</p>
    </div>
  </section>
  <section class="band band-2">
    <div class="portrait" role="img" aria-label="Portrait of Marcus Olden"></div>
    <div class="quote">
      <p class="quote-text">“The most contrarian thing of all is not to oppose the crowd<br>but to think for yourself.”</p>
      <p class="quote-author">- Marcus Olden</p>
    </div>
  </section>
  <section class="band band-3">
    <div class="portrait" role="img" aria-label="Portrait of Frankie Dalgarth"></div>
    <div class="quote">
      <p class="quote-text">“I constantly see people rise in life who are not the smartest, sometimes not even the most diligent, but they are learning machines. They go to bed every night a little wiser than they were when they got up and boy does that help, particularly when you have a long run ahead of you.”</p>
      <p class="quote-author">- Frankie Dalgarth</p>
    </div>
  </section>
  <section class="band band-4">
    <div class="portrait" role="img" aria-label="Portrait of Kees R. T. Ter Haverkamp"></div>
    <div class="quote">
      <p class="quote-text">“In theory, there’s no difference between theory and practice.<br>But, in practice, there is.”</p>
      <p class="quote-author">- Kees R. T. Ter Haverkamp</p>
    </div>
  </section>
  <section class="band band-5">
    <div class="portrait" role="img" aria-label="Portrait of Rohan Kapadia"></div>
    <div class="quote">
      <p class="quote-text">“At the end of the day, a reactionary life is a normal life.<br>One thing is consistent in every remarkable person:<br>they decide to do something remarkable.<br>Don’t let the world choose who you become.”</p>
      <p class="quote-author">- Rohan Kapadia</p>
    </div>
  </section>
  <section class="band band-6">
    <div class="portrait" role="img" aria-label="Portrait of Ned Yarrow"></div>
    <div class="quote">
      <p class="quote-text">“It usually takes 3-4 months to try enough that you can do a<br>proper 80/20 analysis, then two months to design<br>systems to scale what *is* working.”</p>
      <p class="quote-author">-Ned Yarrow</p>
    </div>
  </section>
  <section class="band band-7">
    <div class="portrait" role="img" aria-label="Portrait of Glenn Mosbacker"></div>
    <div class="quote">
      <p class="quote-text">“Authority is 20 percent given, 80 percent taken.”</p>
      <p class="quote-author">- Glenn Mosbacker</p>
    </div>
  </section>
  <section class="band band-8">
    <div class="portrait" role="img" aria-label="Portrait of Dieter Kolbach"></div>
    <div class="quote">
      <p class="quote-text">“Your actions are consistent with the way the world occurs to you.”</p>
      <p class="quote-author">- Dieter Kolbach</p>
    </div>
  </section>
</main>
</body>
</html>
```